One business card required with 2 company logos and 2 people's details

One business card required.
No preference on design - One side could show the 2 different business logos for the companies we own. The reverse could have the details shown below.
Another option could be one business one side and one business on the reverse. Happy to receive designs.

Dora Pellham
07700 913 286
Rowena Tindall
07700 958 137

website: quietmeadowbloom.co.uk
email: info@quietmeadowbloom.co.uk

website: brightharbourevents.co.uk
email: info:brightharbourevents.co.uk

May be nice to have icons instead of the words email/website?

I have included different versions of the logos to help with your design.

Contact Information for Business Card

see project overview

Requirements
Must have
• both company logos, both contact names and contact details

```html
<!DOCTYPE html>
<html lang="en">
<head>
<meta charset="utf-8">
<title>Business Card – Quiet Meadow Bloom &amp; Bright Harbour Events</title>
<link href="https://fonts.googleapis.com/css2?family=Arimo:wght@400;700&display=swap" rel="stylesheet">
<style>
  :root {
    --backdrop: #c9c9c7;
    --card: #ffffff;
    --blue: #3a7bd0;
    --navy: #2e3159;
    --ink: #2b2b33;
    --rule: #2f6cc4;
    --icon: #2a4f9e;
  }
  * { margin: 0; padding: 0; box-sizing: border-box; }
  html, body {
    width: 1200px; height: 801px; overflow: hidden;
    background: var(--backdrop);
    font-family: "Arimo", Arial, sans-serif;
  }
  .stage {
    width: 1200px; height: 801px;
    display: flex; align-items: center; justify-content: center; gap: 48px;
  }
  .card {
    position: relative;
    width: 540px; height: 340px;
    background: var(--card);
    box-shadow: 0 10px 28px rgba(0,0,0,0.18);
  }

  /* details side */
  .people {
    position: absolute; top: 34px; right: 38px;
    text-align: right;
  }
  .person + .person { margin-top: 14px; }
  .person-name { font-weight: 700; font-size: 20px; letter-spacing: -0.3px; line-height: 1.1; }
  .person-name.is-first { color: var(--blue); }
  .person-name.is-second { color: var(--navy); }
  .person-phone { font-size: 13px; color: var(--ink); margin-top: 3px; letter-spacing: 0.4px; }

  .brand {
    display: flex; align-items: center; gap: 8px;
    font-weight: 700; color: var(--navy); line-height: 1.15;
  }
  .brand-dot { flex: none; border-radius: 50%; background: var(--blue); }
  .brand.is-bloom .brand-dot { background: var(--navy); }

  .details .brand.is-bloom { position: absolute; right: 38px; top: 182px; font-size: 17px; }
  .details .brand.is-bloom .brand-dot { width: 14px; height: 14px; }
  .details .brand.is-harbour { position: absolute; left: 34px; top: 150px; font-size: 17px; color: var(--blue); }
  .details .brand.is-harbour .brand-dot { width: 14px; height: 14px; }

  .contacts {
    position: absolute; left: 34px; bottom: 28px;
    list-style: none;
    font-size: 13px; color: var(--ink);
  }
  .contacts li { display: flex; align-items: center; gap: 7px; line-height: 19px; }
  .contacts svg { width: 12px; height: 12px; flex: none; }

  /* logos side */
  .logos { display: flex; align-items: center; }
  .logos .half { flex: 1; height: 100%; display: flex; align-items: center; justify-content: center; }
  .logos .divider { width: 1.5px; height: 170px; background: var(--rule); }
  .logos .brand { font-size: 24px; flex-direction: column; text-align: center; gap: 12px; }
  .logos .brand .brand-dot { width: 22px; height: 22px; }
  .logos .brand.is-harbour { color: var(--blue); }
</style>
</head>
<body>
<main class="stage">

  <section class="card details" aria-label="Card contact side">
    <div class="people">
      <div class="person">
        <p class="person-name is-first">Dora Pellham</p>
        <p class="person-phone">07700 913 286</p>
      </div>
      <div class="person">
        <p class="person-name is-second">Rowena Tindall</p>
        <p class="person-phone">07700 958 137</p>
      </div>
    </div>

    <div class="brand is-bloom"><span class="brand-dot"></span><span>Quiet Meadow Bloom</span></div>
    <div class="brand is-harbour"><span class="brand-dot"></span><span>Bright Harbour Events</span></div>

    <ul class="contacts">
      <li>
        <svg viewBox="0 0 12 12" aria-hidden="true"><rect x="0.5" y="2" width="11" height="8" rx="1" fill="var(--icon)"/><path d="M1 2.6 6 6.6 11 2.6" stroke="#fff" stroke-width="1" fill="none"/></svg>
        info@quietmeadowbloom.co.uk
      </li>
      <li>
        <svg viewBox="0 0 12 12" aria-hidden="true"><rect x="0.5" y="2" width="11" height="8" rx="1" fill="var(--icon)"/><path d="M1 2.6 6 6.6 11 2.6" stroke="#fff" stroke-width="1" fill="none"/></svg>
        info@brightharbourevents.co.uk
      </li>
      <li>
        <svg viewBox="0 0 12 12" aria-hidden="true"><circle cx="6" cy="6" r="5.5" fill="var(--icon)"/><path d="M0.8 6h10.4M6 0.8c-2.4 2.8-2.4 7.6 0 10.4M6 0.8c2.4 2.8 2.4 7.6 0 10.4" stroke="#fff" stroke-width="0.8" fill="none"/></svg>
        quietmeadowbloom.co.uk
      </li>
      <li>
        <svg viewBox="0 0 12 12" aria-hidden="true"><circle cx="6" cy="6" r="5.5" fill="var(--icon)"/><path d="M0.8 6h10.4M6 0.8c-2.4 2.8-2.4 7.6 0 10.4M6 0.8c2.4 2.8 2.4 7.6 0 10.4" stroke="#fff" stroke-width="0.8" fill="none"/></svg>
        brightharbourevents.co.uk
      </li>
    </ul>
  </section>

  <section class="card logos" aria-label="Card logo side">
    <div class="half">
      <div class="brand is-bloom"><span class="brand-dot"></span><span>Quiet Meadow<br>Bloom</span></div>
    </div>
    <div class="divider"></div>
    <div class="half">
      <div class="brand is-harbour"><span class="brand-dot"></span><span>Bright Harbour<br>Events</span></div>
    </div>
  </section>

</main>
</body>
</html>
```